Social Media App Needs PPT Template

We need a PowerPoint template for a new social media company based in the DC area called "Bold Ledger." We provide an interactive digital platform for executives to share actionable advice. We would like to see designs that use our orange logo color as an accent, but are mainly grey, white, and black. The final design should communicate clean, chic, modern, and professional.

Target Market(s)

Executives

Industry/Entity Type

Information Technology

Font styles to use
Sans Serif

Colors
f78f20
fbe7d2
ffffff
000000
e8e8e8
757575

Requirements
Must have
• My project must have title page and many options for the body of the ppt (graphs, tables, etc). It also needs to be easy to modify. I must have someone who is experienced in creating powerpoint templates.
Nice to have
• It would be nice to have a very modern and clean design that includes the logo on every page, but still leaves a lot of room for the content of the slide
Should not have
• My design project should not look to busy.

```html
<!DOCTYPE html>
<html lang="en">
<head>
<meta charset="utf-8">
<title>Bold Ledger – Chart Slide</title>
<link href="https://fonts.googleapis.com/css2?family=Bebas+Neue&family=Lato:wght@400;700&display=swap" rel="stylesheet">
<style>
  :root{
    --stage:#555555;
    --paper:#ffffff;
    --navy:#222d3c;
    --orange:#f39320;
    --charcoal:#555658;
    --silver:#cbcccd;
    --heading-grey:#4a4a4c;
    --body-grey:#7a7a7a;
    --soft-grey:#c4c4c4;
  }
  *{margin:0;padding:0;box-sizing:border-box}
  html,body{width:1200px;height:960px;overflow:hidden;background:var(--stage)}
  body{position:relative;font-family:"Lato",sans-serif}
  .page-label{position:absolute;top:72px;left:0;width:1200px;text-align:center;color:#f2f2f2;font-size:27px;font-weight:400}
  .slide{position:absolute;left:123px;top:159px;width:987px;height:741px;background:var(--paper);overflow:hidden}
  .accent-bar{position:absolute;left:0;top:15px;width:100%;height:12px;background:var(--orange)}
  .header-band{position:absolute;left:0;top:29px;width:100%;height:95px;background:var(--navy)}
  .slide-title{position:absolute;left:42px;top:22px;font-family:"Bebas Neue",sans-serif;font-size:58px;line-height:1;color:#fff;letter-spacing:-0.5px}
  .brand{position:absolute;right:46px;top:36px;display:flex;align-items:center;gap:10px;color:#fff;font-weight:700;font-size:24px;letter-spacing:1.5px}
  .brand-dot{width:22px;height:22px;border-radius:50%;background:var(--orange)}
  .chart-art{position:absolute;left:0;top:0}
  .segment-heading{position:absolute;font-weight:700;font-size:25px;line-height:1;white-space:nowrap}
  .segment-text{position:absolute;font-size:17.6px;line-height:25.6px;color:var(--body-grey);width:260px}
  .h-charcoal{color:var(--heading-grey)}
  .h-orange{color:var(--orange)}
  .h-navy{color:var(--navy)}
  .h-silver{color:var(--soft-grey)}
  .footer-note{position:absolute;right:32px;top:703px;font-size:13.5px;color:var(--body-grey)}
</style>
</head>
<body>
  <div class="page-label">Page 8</div>

  <section class="slide">
    <div class="accent-bar"></div>
    <header class="header-band">
      <h1 class="slide-title">TITLE GOES HERE</h1>
      <div class="brand"><span class="brand-dot"></span>BOLD LEDGER</div>
    </header>

    <svg class="chart-art" width="987" height="741" viewBox="0 0 987 741">
      <g fill="none" stroke-width="1.6">
        <polyline points="54,220 357,220 421,295" stroke="var(--heading-grey)"/>
        <polyline points="914,222 613,222 553,295" stroke="var(--orange)"/>
        <polyline points="49,488 349,488 382,450" stroke="var(--navy)"/>
        <polyline points="923,488 622,488 586,457" stroke="var(--silver)"/>
        <line x1="663" y1="684" x2="954" y2="684" stroke="#555" stroke-width="1.2"/>
      </g>
      <g stroke="#fff" stroke-width="1.5">
        <path d="M367,393 A119,119 0 0 1 486,274 L486,338 A55,55 0 0 0 431,393 Z" fill="var(--charcoal)"/>
        <path d="M486,274 A119,119 0 0 1 605,393 L541,393 A55,55 0 0 0 486,338 Z" fill="var(--orange)"/>
        <path d="M486,512 A119,119 0 0 1 367,393 L431,393 A55,55 0 0 0 486,448 Z" fill="var(--navy)"/>
        <path d="M605,393 A119,119 0 0 1 486,512 L486,448 A55,55 0 0 0 541,393 Z" fill="var(--silver)"/>
      </g>
      <g fill="#fff" font-family="Lato, sans-serif" font-size="21" text-anchor="middle">
        <text x="428" y="343">25%</text>
        <text x="549" y="343">25%</text>
        <text x="428" y="463">25%</text>
        <text x="549" y="463">25%</text>
      </g>
    </svg>

    <h2 class="segment-heading h-charcoal" style="left:54px;top:193px">NOBIS VIDENTUR</h2>
    <p class="segment-text" style="left:54px;top:232px">Lorem ipsum dolor sit amet, consectetuer adipi scing elit, sed diam nonummy nibh euismod tin.</p>

    <h2 class="segment-heading h-orange" style="left:661px;top:193px">NOBIS VIDENTUR</h2>
    <p class="segment-text" style="left:665px;top:232px">Lorem ipsum dolor sit amet, consectetuer adipi scing elit, sed diam nonummy nibh euismod tin.</p>

    <h2 class="segment-heading h-navy" style="left:54px;top:460px">NOBIS VIDENTUR</h2>
    <p class="segment-text" style="left:54px;top:498px">Lorem ipsum dolor sit amet, consectetuer adipi scing elit, sed diam nonummy nibh euismod tin.</p>

    <h2 class="segment-heading h-silver" style="left:675px;top:460px">NOBIS VIDENTUR</h2>
    <p class="segment-text" style="left:675px;top:498px">Lorem ipsum dolor sit amet, consectetuer adipi scing elit, sed diam nonummy nibh euismod tin.</p>

    <footer class="footer-note">www.boldledger.com &nbsp;|&nbsp; Page 6</footer>
  </section>
</body>
</html>
```